Residential building / Apartments for sale landing page

I need a website / landing page design for my latest development project - a residential building with 70+ apartments for sale. I need the design in layers in Photoshop/Illustrator/InDesign format with all the icons/shapes/maps/graphic assets in vector format (svg, ai, eps) as much as possible.

I prefer white website and please consider the performance/coding experience. We're not making something suitable only for a design contest with fancy parallax effects and confusing animations. We're trying to create usable and clean UI with good UX.

The website will be custom coded, i.e. I'm not using WordPress.

I know that the existing 3D photos are not good but for now you can use them or replace them with some stock photos. I'm going to create new 3D photos soon.

Real Estate Development

1 page

```html
<!DOCTYPE html>
<html lang="en">
<head>
<meta charset="utf-8">
<title>Verdant Heights – Residences</title>
<link href="https://fonts.googleapis.com/css2?family=Questrial&family=Arimo:wght@400;700&display=swap" rel="stylesheet">
<style>
:root{
  --green:#8dc63f;
  --ink:#1d1d1d;
  --muted:#7a7a7a;
  --light:#f4f4f4;
  --grey:#e6e6e6;
  --dark:#262626;
  --footer:#1e1e1e;
  --white:#ffffff;
}
*{box-sizing:border-box;margin:0;padding:0}
html,body{width:1200px;height:4728px;overflow:hidden}
body{position:relative;background:var(--white);font-family:'Arimo',Arial,sans-serif;color:var(--ink)}
.abs{position:absolute}
.head-font{font-family:'Questrial',Arial,sans-serif}
.eyebrow{font-size:11px;letter-spacing:5px;text-transform:uppercase;color:var(--ink)}
.title{font-family:'Questrial',Arial,sans-serif;font-weight:400;color:var(--ink)}
.para{font-size:11.5px;line-height:16px;color:var(--muted)}
.btn{display:flex;align-items:center;gap:18px}
.btn span{background:var(--ink);color:#fff;font-size:12px;padding:4px 9px;border-bottom:3px solid var(--ink);box-shadow:0 4px 0 -1px #fff,0 5px 0 0 var(--ink)}
.photo{display:block}

/* header */
.site-header{left:0;top:0;width:1200px;height:106px;background:#fff}
.brand{left:46px;top:40px;display:flex;align-items:center;gap:8px;font-family:'Questrial',Arial,sans-serif;font-size:22px;color:var(--ink);letter-spacing:1px}
.brand i{width:14px;height:14px;background:var(--green);display:block}
.nav a{position:absolute;top:47px;font-size:13px;font-weight:700;color:var(--ink);text-decoration:none}
.nav a.active{color:var(--green)}
.nav .icon-link{display:flex;align-items:center;gap:6px}

/* hero */
.hero{left:0;top:106px;width:1200px;height:610px;background:linear-gradient(180deg,#7b8a7e 0%,#a9b6a6 30%,#6f8a55 65%,#4d5f3a 100%)}
.hero-play{left:547px;top:373px;width:106px;height:106px;border-radius:50%;background:rgba(255,255,255,.9)}
.hero-sub{left:0;width:1200px;top:590px;text-align:center;font-size:31px;color:#fff;text-shadow:0 2px 6px rgba(0,0,0,.5)}
.hero-title{left:0;width:1200px;top:630px;text-align:center;font-size:50px;color:#fff;text-shadow:0 3px 8px rgba(0,0,0,.6)}
.hero-down{left:1112px;top:620px;width:42px;height:74px;border:2px solid #fff}

/* intro */
.band{left:0;top:716px;width:1200px;height:50px;background:var(--grey)}
.intro{left:0;top:766px;width:1200px;height:620px;background:#e4e4e4}

/* services */
.services{left:0;top:1386px;width:1200px;height:678px;background:var(--light)}
.green-block{left:0;top:1453px;width:318px;height:542px;background:var(--green)}
.thumb{left:604px;width:80px;height:78px}
.zoom{left:523px;top:1886px;width:62px;height:60px;background:#fff}

/* featuring */
.featuring{left:0;top:2064px;width:1200px;height:665px;background:#ebebeb}
.room{top:2132px;width:254px;height:521px}
.room-label{position:absolute;left:20px;top:392px;font-family:'Arimo',Arial,sans-serif;font-weight:700;font-size:36px;line-height:38px;color:#fff}
.room-text{position:absolute;left:20px;top:470px;width:220px;font-size:9px;line-height:11px;color:#fff}
.room-bar{position:absolute;left:24px;bottom:0;width:66px;height:6px;background:var(--green)}

/* floor plan */
.plans{left:0;top:2729px;width:1200px;height:767px;background:#f5f5f5}
.spec{display:flex;align-items:center;gap:18px;width:188px;height:64px;border-bottom:1px solid #dcdcdc}
.spec b{display:block;font-size:13px;font-weight:700;color:var(--ink)}
.spec small{display:block;font-size:10px;color:var(--green);margin-top:3px}

/* dark */
.dark{left:0;top:3496px;width:1200px;height:284px;background:var(--dark);overflow:hidden}
.dark-word{left:0;width:1200px;top:18px;text-align:center;font-family:'Arimo',Arial,sans-serif;font-weight:700;font-size:150px;color:#2f2f2f;letter-spacing:6px;white-space:nowrap}
.tile{width:240px;height:161px}

/* partners */
.partners{left:0;top:4101px;width:1200px;height:125px;background:#fff}
.partner{top:4148px;width:110px;height:30px;border-radius:15px;background:#d4d4d4}

/* footer */
.site-footer{left:0;top:4226px;width:1200px;height:502px;background:var(--footer)}
.foot-title{font-family:'Arimo',Arial,sans-serif;font-weight:700;font-size:28px;color:var(--green)}
.foot-text{font-size:14px;line-height:18px;color:#fff}
.legal a{position:absolute;top:4694px;font-size:11px;color:#444;text-decoration:none;letter-spacing:1px}
</style>
</head>
<body>

<header class="abs site-header">
  <div class="abs brand"><i></i>VERDANT HEIGHTS</div>
  <nav class="nav">
    <a class="active" style="left:446px">About</a>
    <a style="left:540px">Experiences</a>
    <a style="left:678px">Residences</a>
    <a class="icon-link" style="left:960px"><svg width="20" height="20" viewBox="0 0 20 20"><circle cx="10" cy="10" r="9" fill="var(--ink)"/><circle cx="10" cy="8" r="3.5" fill="#fff"/><path d="M4 16c2-4 10-4 12 0" fill="#fff"/></svg>Sign up</a>
    <a class="icon-link" style="left:1075px"><svg width="20" height="16" viewBox="0 0 20 16"><rect x="1" y="1" width="18" height="14" fill="none" stroke="var(--ink)" stroke-width="1.5"/><path d="M1 1l9 8 9-8" fill="none" stroke="var(--ink)" stroke-width="1.5"/></svg>contact</a>
  </nav>
</header>

<section class="abs hero" role="img" aria-label="Rendering of terraced green residential towers with planted balconies along a hillside street"></section>
<div class="abs hero-play"><svg width="106" height="106" viewBox="0 0 106 106"><path d="M42 33l30 20-30 20z" fill="#333"/></svg></div>
<p class="abs hero-sub head-font">Appartment You'll Love!</p>
<h1 class="abs hero-title head-font" style="font-weight:400">THE BEST PLACE TO CALL HOME</h1>
<div class="abs hero-down"><svg width="38" height="70" viewBox="0 0 38 70"><path d="M19 14v40M10 45l9 10 9-10" fill="none" stroke="#fff" stroke-width="2"/></svg></div>

<div class="abs band"></div>
<section class="abs intro">
  <svg class="abs" style="left:0;top:0" width="1200" height="620" viewBox="0 0 1200 620">
    <defs>
      <linearGradient id="greenhouse" x1="0" y1="0" x2="1" y2="1">
        <stop offset="0" stop-color="#8ea17e"/><stop offset=".5" stop-color="#5f7c43"/><stop offset="1" stop-color="#b7c2a6"/>
      </linearGradient>
    </defs>
    <polygon points="0,0 310,0 0,270" fill="#ececec"/>
    <polygon points="660,0 1200,0 1200,530 915,300" fill="url(#greenhouse)" role="img" aria-label="Greenhouse interior with hanging plants and potted flowers"/>
    <line x1="611" y1="0" x2="915" y2="305" stroke="var(--ink)" stroke-width="3"/>
  </svg>
  <p class="abs eyebrow" style="left:48px;top:216px">Since 1991</p>
  <h2 class="abs title" style="left:48px;top:236px;font-size:43px;line-height:58px">TRANSFORMING HOMES<br>AND LIVES</h2>
  <p class="abs" style="left:48px;top:388px;font-size:15px;color:var(--muted)">Creating sustainable communities, designed to inspire.</p>
  <div class="abs btn" style="left:48px;top:434px"><span>READ MORE</span><svg width="28" height="12" viewBox="0 0 28 12"><path d="M0 6h26M21 1l5 5-5 5" fill="none" stroke="var(--ink)" stroke-width="1.6"/></svg></div>
</section>

<section class="abs services">
  <div class="abs green-block" style="top:67px"></div>
  <div class="abs photo" style="left:50px;top:115px;width:535px;height:444px;background:linear-gradient(160deg,#8a5a32,#c08a50 45%,#6b3d1e)" role="img" aria-label="Open kitchen with wooden cabinets, granite island and bar stools"></div>
  <div class="abs zoom" style="top:500px"><svg width="62" height="60" viewBox="0 0 62 60"><circle cx="28" cy="27" r="9" fill="none" stroke="var(--ink)" stroke-width="2.5"/><path d="M35 34l8 8" stroke="var(--ink)" stroke-width="3"/></svg></div>
  <div class="abs thumb" style="top:210px;background:linear-gradient(#d8dcd8,#a8b0a6)" role="img" aria-label="Thumbnail of a bright window view"></div>
  <div class="abs thumb" style="top:297px;background:linear-gradient(#c6915a,#7a4a26)" role="img" aria-label="Thumbnail of the kitchen"></div>
  <div class="abs thumb" style="top:381px;background:linear-gradient(#f0f0f0,#d6d6d6)" role="img" aria-label="Thumbnail of a white bathroom"></div>
  <p class="abs eyebrow" style="left:778px;top:210px">Our Services</p>
  <h2 class="abs title" style="left:778px;top:236px;font-size:29px;line-height:36px">More than 20+ years of<br>Achievements</h2>
  <p class="abs para" style="left:778px;top:326px;width:338px">Lorem ipsum dolor sit amet, consectetur adipiscing elit, sed do eiusmod tempor incididunt ut labore et dolore magna aliqua. Ut enim ad minim veniam, quis nostrud exercitation ullamco laboris nisi ut aliquip ex ea commodo consequat.</p>
  <div class="abs btn" style="left:778px;top:436px"><span>READ MORE</span><svg width="28" height="12" viewBox="0 0 28 12"><path d="M0 6h26M21 1l5 5-5 5" fill="none" stroke="var(--ink)" stroke-width="1.6"/></svg></div>
</section>

<section class="abs featuring">
  <p class="abs eyebrow" style="left:50px;top:204px">Featuring</p>
  <h2 class="abs title" style="left:50px;top:226px;font-size:29px;line-height:36px">Feel The Luxury And<br>Comfort</h2>
  <p class="abs para" style="left:50px;top:318px;width:318px">Lorem ipsum dolor sit amet, consectetur adipiscing elit, sed do eiusmod tempor incididunt ut labore et dolore magna aliqua. Ut enim ad minim veniam, quis nostrud exercitation ullamco laboris nisi ut aliquip ex ea commodo consequat.</p>
  <div class="abs btn" style="left:50px;top:424px"><span>READ MORE</span><svg width="28" height="12" viewBox="0 0 28 12"><path d="M0 6h26M21 1l5 5-5 5" fill="none" stroke="var(--ink)" stroke-width="1.6"/></svg></div>
</section>
<article class="abs room" style="left:439px;background:linear-gradient(180deg,#5a5a5a,#2e2e2e)" role="img" aria-label="Black and white living room with armchair and curtains">
  <h3 class="room-label">LIVING<br>ROOM</h3><p class="room-text">Lorem ipsum dolor sit amet, consectetur adipiscing elit, sed do eiusmod tempor incididunt</p><i class="room-bar"></i>
</article>
<article class="abs room" style="left:693px;background:linear-gradient(180deg,#9a9a9a,#4c4c4c)" role="img" aria-label="Black and white kitchen with dining table and pendant light">
  <h3 class="room-label">KITCHEN</h3><p class="room-text">Lorem ipsum dolor sit amet, consectetur adipiscing elit, sed do eiusmod tempor incididunt</p><i class="room-bar"></i>
</article>
<article class="abs room" style="left:946px;background:linear-gradient(180deg,#8c8c8c,#3e3e3e)" role="img" aria-label="Black and white bathroom with freestanding tub">
  <h3 class="room-label">LIVING<br>ROOM</h3><p class="room-text">Lorem ipsum dolor sit amet, consectetur adipiscing elit, sed do eiusmod tempor incididunt</p><i class="room-bar"></i>
</article>

<section class="abs plans">
  <p class="abs eyebrow" style="left:0;width:1200px;text-align:center;top:66px;font-size:10px">Our Project</p>
  <h2 class="abs title" style="left:0;width:1200px;text-align:center;top:110px;font-size:29px;line-height:36px">Amazing Floor Planning For<br>Your Comfort</h2>
  <p class="abs para" style="left:240px;width:720px;text-align:center;top:200px">Lorem ipsum dolor sit amet, consectetur adipiscing elit, sed do eiusmod tempor incididunt ut labore et dolore magna aliqua. Ut enim ad minim veniam, quis nostrud exercitation ullamco laboris nisi.</p>
  <div class="abs photo" style="left:279px;top:300px;width:638px;height:375px;background:linear-gradient(135deg,#f2f2f2,#cfcfcf 50%,#5c5652)" role="img" aria-label="3D floor plan of an apartment with furnished rooms"></div>

  <div class="abs" style="left:50px;top:290px">
    <div class="spec"><svg width="26" height="26"><rect x="3" y="6" width="20" height="12" fill="none" stroke="var(--ink)" stroke-width="2"/><path d="M13 18v6M6 24h14" stroke="var(--ink)" stroke-width="2"/></svg><div><b>Living Room</b><small>2.85 x 3 METER</small></div></div>
    <div class="spec"><svg width="26" height="26"><path d="M9 3h8v8l6 12H3l6-12z" fill="none" stroke="var(--ink)" stroke-width="2"/></svg><div><b>Kitchen</b><small>2.85 x 3 METER</small></div></div>
    <div class="spec"><svg width="26" height="26"><path d="M2 10h22M5 10v14M21 10v14M2 4v20M24 4v20" stroke="var(--ink)" stroke-width="2.5"/></svg><div><b>Dining Room</b><small>2.85 x 3 METER</small></div></div>
    <div class="spec"><svg width="26" height="26"><rect x="2" y="9" width="22" height="10" rx="3" fill="var(--ink)"/><path d="M3 19v4M23 19v4" stroke="var(--ink)" stroke-width="2"/></svg><div><b>Master Bedroom</b><small>2.85 x 3 METER</small></div></div>
    <div class="spec"><svg width="26" height="26"><rect x="5" y="4" width="16" height="10" fill="var(--ink)"/><path d="M3 14h20v9M3 14v9" stroke="var(--ink)" stroke-width="2.5" fill="none"/></svg><div><b>Bedroom</b><small>2.85 x 3 METER</small></div></div>
  </div>
  <div class="abs" style="left:960px;top:290px">
    <div class="spec"><svg width="26" height="26"><path d="M2 8h22c0 9-5 12-11 12S2 17 2 8z" fill="var(--ink)"/></svg><div><b>Bedroom</b><small>2.85 x 3 METER</small></div></div>
    <div class="spec"><svg width="26" height="26"><path d="M5 2v22M21 2v22M5 7h16M5 13h16M5 19h16" stroke="var(--ink)" stroke-width="2.5"/></svg><div><b>Bathroom</b><small>2.85 x 3 METER</small></div></div>
    <div class="spec"><svg width="26" height="26"><rect x="6" y="3" width="14" height="10" rx="3" fill="#666"/><rect x="3" y="12" width="20" height="8" rx="2" fill="#555"/><path d="M6 20v4M20 20v4" stroke="#555" stroke-width="2"/></svg><div><b>Guest Bathroom</b><small>2.85 x 3 METER</small></div></div>
    <div class="spec"><svg width="26" height="26"><rect x="3" y="4" width="20" height="12" fill="none" stroke="var(--ink)" stroke-width="2"/><path d="M13 16v6M6 23h14" stroke="var(--ink)" stroke-width="2"/></svg><div><b>Dining Room</b><small>2.85 x 3 METER</small></div></div>
    <div class="spec"><svg width="26" height="26"><path d="M3 11L13 3l10 8v13H3z" fill="none" stroke="var(--ink)" stroke-width="2"/><path d="M7 15h12M7 19h12" stroke="var(--ink)" stroke-width="2"/></svg><div><b>Living Room</b><small>2.85 x 3 METER</small></div></div>
  </div>
</section>

<section class="abs dark">
  <div class="abs dark-word">LUXURY HOMES</div>
  <p class="abs eyebrow" style="left:0;width:1200px;text-align:center;top:62px;font-size:10px;color:var(--green)">Our Project</p>
  <h2 class="abs title" style="left:0;width:1200px;text-align:center;top:106px;font-size:29px;line-height:36px;color:#fff">Amazing Floor Planning For<br>Your Comfort</h2>
  <p class="abs para" style="left:240px;width:720px;text-align:center;top:192px;color:#555">Lorem ipsum dolor sit amet, consectetur adipiscing elit, sed do eiusmod tempor incididunt ut labore et dolore magna aliqua. Ut enim ad minim veniam, quis nostrud exercitation ullamco laboris nisi.</p>
</section>

<div class="abs tile" style="left:0;top:3780px;background:linear-gradient(#e8e8e8,#b8b3ad)" role="img" aria-label="White kitchen interior"></div>
<div class="abs tile" style="left:240px;top:3780px;background:linear-gradient(#5d8fd2,#3a3a3a)" role="img" aria-label="Modern house exterior at dusk"></div>
<div class="abs tile" style="left:480px;top:3780px;background:linear-gradient(#3f6b35,#7b5a3a)" role="img" aria-label="Tall windows with garden view"></div>
<div class="abs tile" style="left:720px;top:3780px;background:linear-gradient(#4b4f55,#2d4a5a)" role="img" aria-label="Living room with tufted sofa"></div>
<div class="abs tile" style="left:960px;top:3780px;background:linear-gradient(#8a6a4a,#c9a47a)" role="img" aria-label="Open plan dining area with chandelier"></div>
<div class="abs tile" style="left:0;top:3941px;background:linear-gradient(#d8d8d8,#6d7a68)" role="img" aria-label="Bathroom with freestanding tub"></div>
<div class="abs tile" style="left:240px;top:3941px;background:linear-gradient(#9a6236,#c08a50)" role="img" aria-label="Wooden kitchen with island"></div>
<div class="abs tile" style="left:480px;top:3941px;background:linear-gradient(#8a7a6a,#d0c6b8)" role="img" aria-label="Lounge with sofas and fireplace"></div>
<div class="abs tile" style="left:720px;top:3941px;background:linear-gradient(#f0f0f0,#a6a6a6)" role="img" aria-label="Bright white kitchen with island"></div>
<div class="abs tile" style="left:960px;top:3941px;background:linear-gradient(#5d8fd2,#2e2e2e)" role="img" aria-label="Contemporary villa with glass balconies"></div>

<section class="abs partners" aria-label="Partners"></section>
<div class="abs partner" style="left:61px"></div>
<div class="abs partner" style="left:257px"></div>
<div class="abs partner" style="left:455px"></div>
<div class="abs partner" style="left:651px"></div>
<div class="abs partner" style="left:848px"></div>
<div class="abs partner" style="left:1046px;width:60px;left:1071px"></div>

<footer class="abs site-footer">
  <h3 class="abs foot-title" style="left:77px;top:90px">INVITATIONS</h3>
  <p class="abs foot-text" style="left:77px;top:138px;width:220px">If you would like to be invited to our events, please subscribe to our mailing list.</p>
  <div class="abs" style="left:77px;top:226px;width:138px;height:34px;background:#fff;font-size:12px;color:#999;padding:10px 12px">EMAIL</div>
  <div class="abs" style="left:215px;top:226px;width:79px;height:34px;background:var(--green);font-size:12px;font-weight:700;color:var(--ink);padding:10px 0;text-align:center">SUBMIT</div>

  <h3 class="abs foot-title" style="left:483px;top:90px">CONTACT</h3>
  <p class="abs foot-text" style="left:483px;top:136px;width:260px">Linden &amp; Roe Interior Planning Ltd<br>Harbor Lane 14, 2040 Eastbrook<br>+00 1/234 56 78<br>hello [at] lindenroe.example</p>

  <h3 class="abs foot-title" style="left:888px;top:90px">OPENING HOURS</h3>
  <p class="abs foot-text" style="left:888px;top:136px;width:240px">Customer and viewing appointments are possible with us at any time while observing all safety precautions<br><br>We ask for an appointment!</p>

  <div class="abs" style="left:0;width:1200px;top:370px;display:flex;justify-content:center;align-items:center;gap:14px;font-family:'Arimo',Arial,sans-serif;font-weight:700;font-size:42px;color:#fff;letter-spacing:1px"><i style="width:22px;height:22px;background:var(--green);display:block"></i>VERDANT HEIGHTS</div>
</footer>
<nav class="legal">
  <a style="left:316px">MODERN SLAVERY POLICY</a>
  <a style="left:517px">POLICY STATEMENTS</a>
  <a style="left:684px">PRIVACY NOTICE</a>
  <a style="left:825px">COOKIES</a>
</nav>

</body>
</html>
```